New Business Card Design for Manufacturing

We are an engineering/manufacturing company that offers Advanced machining/assembly/engineering services, as well as innovative products for the heavy duty engine cooling markets.

We are looking to get a new business card designed that is clean and modern looking, but still fits the wide range of technical/skilled work we do.

- We hope to use this design as the base for other design work in new Presentations, web, and print work.

Industry/Entity Type

Engineering

Contact Information for Business Card

Our preferred color of blue is (RGB) 22/71/159 but can vary slightly from that color. Our content will be our Logo and full company name (Vantrell Forge Works, Inc.), company address, name, job title, phone number with extension, cell number, fax number, website, and email address on the cards.
We'd like the full company name next to the logo, but we are open to other interpretations of that layout.
Preferably, we would like the back side to be clean with just our logo, and the front to contain all of the contact information.

Colors
2f74b4
0355a3
85abd2

Requirements
Must have
• - Logo, company name, needed content - We are open to interpretation beyond that.
• - Standard size business card.
• - Horizontal orientation.
• - Enough space for lengthy names / job titles (for example, a job title could read "Directory of Human Resources" or "V.P. of Governmental Affairs"). We need this to look clean, whether the title be short (CEO) or long (as described above).

```html
<!DOCTYPE html>
<html lang="en">
<head>
<meta charset="utf-8">
<title>Vantrell Forge Works – Business Card</title>
<link rel="stylesheet" href="https://fonts.googleapis.com/css2?family=Roboto+Condensed:wght@400;700&family=Exo+2:ital,wght@0,800;1,800&family=Roboto:wght@400;500&display=swap">
<style>
  :root {
    --brand-blue: #1052a3;
    --brand-grey: #7d868e;
    --card-white: #f7f7f7;
    --ink: #1d1d1d;
    --muted: #555a60;
    --backdrop: #e8e6e3;
  }
  * { margin: 0; padding: 0; box-sizing: border-box; }
  html, body { width: 1200px; height: 960px; overflow: hidden; background: var(--backdrop); }
  .card {
    position: absolute;
    width: 600px;
    height: 342px;
    border-radius: 18px;
    overflow: hidden;
    box-shadow: 0 3px 8px rgba(0,0,0,0.25);
  }
  .card--front { left: 302px; top: 130px; background: var(--card-white); }
  .card--back { left: 300px; top: 490px; background: var(--brand-blue); }
  .front-swoosh { position: absolute; inset: 0; }

  .wordmark {
    position: absolute;
    font-family: "Roboto Condensed", sans-serif;
    font-weight: 700;
    text-transform: uppercase;
    line-height: 1;
    white-space: nowrap;
  }
  .card--front .wordmark { left: 46px; top: 66px; font-size: 52px; letter-spacing: 0.5px; color: var(--brand-blue); }
  .tagline {
    position: absolute;
    font-family: "Exo 2", sans-serif;
    font-style: italic;
    font-weight: 800;
    text-transform: uppercase;
    font-size: 14px;
    letter-spacing: 0.2px;
    white-space: nowrap;
  }
  .card--front .tagline { left: 47px; top: 128px; color: var(--brand-grey); }

  .company-name {
    position: absolute;
    left: 302px; top: 55px;
    font-family: "Exo 2", sans-serif;
    font-style: italic;
    font-weight: 800;
    font-size: 19.5px;
    line-height: 21px;
    color: var(--brand-blue);
    text-transform: uppercase;
    white-space: nowrap;
  }
  .company-name small { font-size: 10px; }

  .contact { position: absolute; left: 302px; top: 128px; font-family: "Roboto Condensed", sans-serif; }
  .contact__name { font-size: 22px; font-weight: 400; color: var(--brand-blue); line-height: 26px; }
  .contact__title { font-size: 14px; color: var(--ink); line-height: 18px; }
  .contact__address { margin-top: 8px; font-size: 14px; color: var(--muted); line-height: 18px; }
  .contact__lines { margin-top: 8px; list-style: none; font-size: 14px; color: var(--muted); line-height: 19px; }
  .contact__lines li { display: flex; align-items: center; gap: 7px; }
  .contact__lines svg { width: 13px; height: 13px; fill: var(--brand-blue); flex: none; }

  .card--back .wordmark { left: 0; right: 0; top: 112px; text-align: center; font-size: 80px; letter-spacing: 1px; color: #ffffff; }
  .card--back .tagline { left: 0; right: 0; top: 203px; text-align: center; font-size: 18px; color: #ffffff; }
  .back-web {
    position: absolute; left: 0; right: 0; top: 282px;
    text-align: center;
    font-family: "Roboto", sans-serif;
    font-size: 14px; font-weight: 500;
    letter-spacing: 2.4px;
    color: #ffffff;
  }
</style>
</head>
<body>
  <section class="card card--front" aria-label="Business card front">
    <svg class="front-swoosh" viewBox="0 0 600 342" aria-hidden="true">
      <path d="M392,0 C480,18 578,72 600,152 L600,0 Z" fill="var(--brand-grey)"/>
      <path d="M0,168 C38,258 140,318 292,342 L0,342 Z" fill="var(--brand-blue)"/>
    </svg>
    <div class="wordmark">Vantrell</div>
    <div class="tagline">Built for What's Next</div>
    <h1 class="company-name">Vantrell<br>Forge<br>Works <small>Inc</small></h1>
    <div class="contact">
      <div class="contact__name">DORIAN HALE</div>
      <div class="contact__title">V.P. of Governmental Affairs</div>
      <div class="contact__address">4120 Larkspur Road<br>Juneau, Alaska 34570</div>
      <ul class="contact__lines">
        <li><svg viewBox="0 0 16 16"><path d="M3.5 1l2.5 3-1.5 1.8c.9 2 2.6 3.8 4.7 4.7L11 9l3 2.5-1.5 2.8C7 14 2 9 1.7 3z"/></svg>555 410 2871</li>
        <li><svg viewBox="0 0 16 16"><path d="M4.5 0h7a1 1 0 011 1v14a1 1 0 01-1 1h-7a1 1 0 01-1-1V1a1 1 0 011-1zm.7 2v10h5.6V2zM8 13a1 1 0 100 2 1 1 0 000-2z"/></svg>555 732 6408</li>
        <li><svg viewBox="0 0 16 16"><path d="M1 3h14v1.2L8 9 1 4.2zm0 2.6l7 4.8 7-4.8V13H1z"/></svg>dorian@vantrellforgeworks.com</li>
        <li><svg viewBox="0 0 16 16"><circle cx="8" cy="8" r="7"/><path d="M4 5c2 0 2 2 4 2s1 3 0 4-3 0-3-2-2-1-1-4zM10 3c1 1 3 1 3 3s-2 1-2 0-2-1-1-3z" fill="#fff"/></svg>www.vantrellforgeworks.com</li>
      </ul>
    </div>
  </section>

  <section class="card card--back" aria-label="Business card back">
    <div class="wordmark">Vantrell</div>
    <div class="tagline">Built for What's Next</div>
    <div class="back-web">www.vantrellforgeworks.com</div>
  </section>
</body>
</html>
```